Business card design Needed for new logo / Construction business, home extensions and new builds

We need a business card design using our new logo files which i will attach to this project :)

We are a small construction business specialising in home extensions, new builds and property development. We are very ambitious and would appreciate professional and elegant designs for our new business card.

Very serious about using the services on MakerQuarry and recently acquired our new logo from here :)

Please get involved, i will feedback when i can as i am very busy but can respond daily, thanks

Target Market(s)

People that want to build onto their houses, new building developments or adding too their existing property

Industry/Entity Type

Construction

Contact Information for Business Card

Renwick Tolliver Construction, Lionel Ashby (Managing Director), Tel 07822254961, email - info@renwick-tolliver, www.renwick-tolliver.co.uk

Colors

Designer to choose colors to be used in the design.

Requirements
Must have
• I like a deep grey on the back please. A lot of you have provided black from and back, try mixing things up a little. The black looks cool 😎 Thanks

```html
<!DOCTYPE html>
<html lang="en">
<head>
<meta charset="utf-8">
<title>Renwick Tolliver Construction – Business Card</title>
<link href="https://fonts.googleapis.com/css2?family=Open+Sans:wght@400;600;700&display=swap" rel="stylesheet">
<style>
  :root {
    --stage: #232323;
    --card-front: #1f1f22;
    --card-back: #6d7072;
    --back-mark: #4f5254;
    --gold: #e0a526;
    --gold-light: #f6cf62;
    --gold-dark: #b27a12;
    --silver: #d9dbdd;
    --silver-light: #f4f5f6;
    --silver-dark: #9a9da0;
    --text-light: #f2f2f2;
  }
  * { box-sizing: border-box; margin: 0; padding: 0; }
  html, body {
    width: 1200px; height: 780px; overflow: hidden;
    background: var(--stage);
    font-family: "Open Sans", Arial, sans-serif;
  }
  .stage {
    width: 1200px; height: 780px;
    display: flex; align-items: center; justify-content: center; gap: 40px;
  }
  .card {
    position: relative;
    width: 540px; height: 308px;
    border-radius: 18px;
    overflow: hidden;
    box-shadow: 0 14px 30px rgba(0,0,0,.55);
  }

  /* Back */
  .card-back {
    background: var(--card-back);
    display: flex; align-items: center; justify-content: center;
  }
  .back-brand {
    display: flex; align-items: center; gap: 14px;
    color: var(--back-mark);
    font-weight: 700; font-size: 22px; letter-spacing: 2px;
    text-transform: uppercase; line-height: 1.25;
  }
  .back-brand .brand-square {
    width: 34px; height: 34px; background: var(--back-mark);
  }

  /* Front */
  .card-front { background: var(--card-front); color: var(--text-light); }
  .front-brand {
    position: absolute; left: 34px; top: 98px; width: 200px;
    display: flex; align-items: center; gap: 12px;
    color: var(--silver);
    font-weight: 700; font-size: 15px; letter-spacing: 1.5px;
    text-transform: uppercase; line-height: 1.35;
  }
  .front-brand .brand-square {
    flex: none; width: 26px; height: 26px; background: var(--gold);
  }
  .divider {
    position: absolute; left: 258px; top: 36px;
    width: 1px; height: 150px;
    background: linear-gradient(to bottom, rgba(255,255,255,.1), var(--silver), rgba(255,255,255,.1));
  }
  .contact-block { position: absolute; left: 284px; top: 38px; }
  .person-name { font-weight: 700; font-size: 25px; line-height: 1.1; }
  .person-name .first { color: var(--silver); }
  .person-name .last { color: var(--gold); }
  .person-role { font-size: 12px; font-weight: 600; margin-top: 3px; }
  .contact-list { list-style: none; margin-top: 22px; }
  .contact-list li {
    display: flex; align-items: center; gap: 8px;
    font-size: 12.5px; line-height: 1.65;
  }
  .contact-list svg { width: 12px; height: 12px; flex: none; }
  .address {
    position: absolute; left: 34px; bottom: 42px;
    font-size: 13px; letter-spacing: .2px;
  }
  .edge-band { position: absolute; left: 0; bottom: 0; width: 540px; height: 24px; }
</style>
</head>
<body>
<main class="stage">

  <section class="card card-back" aria-label="Card back">
    <div class="back-brand">
      <span class="brand-square"></span>
      <span>Renwick Tolliver<br>Construction</span>
    </div>
  </section>

  <section class="card card-front" aria-label="Card front">
    <div class="front-brand">
      <span class="brand-square"></span>
      <span>Renwick Tolliver<br>Construction</span>
    </div>

    <div class="divider"></div>

    <div class="contact-block">
      <h1 class="person-name"><span class="first">Lionel</span> <span class="last">Ashby</span></h1>
      <p class="person-role">Managing Director</p>
      <ul class="contact-list">
        <li>
          <svg viewBox="0 0 24 24" fill="var(--gold)" aria-hidden="true"><path d="M6.6 10.8a15.1 15.1 0 0 0 6.6 6.6l2.2-2.2a1 1 0 0 1 1-.25 11.4 11.4 0 0 0 3.6.57 1 1 0 0 1 1 1V20a1 1 0 0 1-1 1A17 17 0 0 1 3 4a1 1 0 0 1 1-1h3.5a1 1 0 0 1 1 1c0 1.25.2 2.45.57 3.57a1 1 0 0 1-.25 1z"/></svg>
          0782 225 4961
        </li>
        <li>
          <svg viewBox="0 0 24 24" fill="none" stroke="var(--gold)" stroke-width="2.2" aria-hidden="true"><circle cx="12" cy="12" r="9.5"/><path d="M2.5 12h19M12 2.5c3 3 3 16 0 19M12 2.5c-3 3-3 16 0 19"/></svg>
          info@renwick-tolliver.co.uk
        </li>
        <li>
          <svg viewBox="0 0 24 24" fill="none" stroke="var(--gold)" stroke-width="2.2" aria-hidden="true"><rect x="2.5" y="5" width="19" height="14" rx="1.5"/><path d="M3 6l9 7 9-7"/></svg>
          www.renwick-tolliver.co.uk
        </li>
      </ul>
    </div>

    <p class="address">Tansley Road, Elmridge Dorsetvale, DV4 2KT</p>

    <svg class="edge-band" viewBox="0 0 540 24" preserveAspectRatio="none" aria-hidden="true">
      <defs>
        <linearGradient id="goldFill" x1="0" y1="0" x2="0" y2="1">
          <stop offset="0" stop-color="var(--gold-light)"/>
          <stop offset=".55" stop-color="var(--gold)"/>
          <stop offset="1" stop-color="var(--gold-dark)"/>
        </linearGradient>
        <linearGradient id="silverFill" x1="0" y1="0" x2="0" y2="1">
          <stop offset="0" stop-color="var(--silver-light)"/>
          <stop offset=".55" stop-color="var(--silver)"/>
          <stop offset="1" stop-color="var(--silver-dark)"/>
        </linearGradient>
      </defs>
      <polygon points="0,6 248,6 262,24 0,24" fill="url(#goldFill)"/>
      <polygon points="236,0 540,0 540,24 262,24" fill="url(#silverFill)"/>
    </svg>
  </section>

</main>
</body>
</html>
```